Clear Plastic Card Design

I am looking to have a business card designed from my logo icon. I am looking to match the style of a different business card I have attached in the files.
Looking for a card that is plastic, with layers of transparency in the shape of my logo icon (also attached in the files) - not a circle like the other card. The winning design will incorporate the red icon logo on the front and back and include the charity's name, "Light for the Weary Souls" in the same or similar font, as well as an email and phone number. For now, use the email: email@lightfortheweary-mail.org and the phone number 555-382-7194.
We like how the sample business card has transparency, partial and full opacity layers and a matching color scheme. Files will need to be in vector so that our business card printing company can work with it.
UPDATE:
We've some excellent designs in, thank you everyone! I got an early review from the owner, and he requested a minor redirect to find his perfect design. He wants the design to stand out by NOT being a rectangle. Try instead a circle, square, or best yet - something that falls in the outline of the logo icon, either fully or partially. Thank you, everyone!
Light for the Weary Souls text should be incorporated as well as a phone and email.

```html
<!DOCTYPE html>
<html lang="en">
<head>
<meta charset="utf-8">
<title>Light for the Weary Souls – Round Clear Card</title>
<link href="https://fonts.googleapis.com/css2?family=Questrial&display=swap" rel="stylesheet">
<style>
  :root {
    --backdrop: #d6cdbf;
    --card-black: #0c0c0e;
    --ring-orange: #d5552b;
    --ring-red: #b3171f;
    --clear-window: #ece6dc;
    --ring-text: #eee3d6;
    --name-red: #bf2126;
  }
  html, body {
    margin: 0;
    padding: 0;
    width: 1200px;
    height: 1008px;
    overflow: hidden;
    background: var(--backdrop);
  }
  .canvas {
    position: relative;
    width: 1200px;
    height: 1008px;
  }
  .round-card {
    display: block;
    width: 1200px;
    height: 1008px;
  }
  .ring-label {
    font-family: "Questrial", "Century Gothic", sans-serif;
    fill: var(--ring-text);
  }
  .ring-label--title { font-size: 33px; letter-spacing: 2px; }
  .ring-label--contact { font-size: 23px; letter-spacing: 1px; }
  .center-name {
    font-family: "Questrial", "Century Gothic", sans-serif;
    font-size: 46px;
    fill: var(--name-red);
  }
</style>
</head>
<body>
<main class="canvas">
  <svg class="round-card" viewBox="0 0 1200 1008" xmlns="http://www.w3.org/2000/svg" aria-label="Round clear business card for Light for the Weary Souls">
    <defs>
      <linearGradient id="ringGradient" x1="0.8" y1="0.1" x2="0.3" y2="1">
        <stop offset="0" stop-color="var(--ring-orange)"/>
        <stop offset="1" stop-color="var(--ring-red)"/>
      </linearGradient>
      <path id="titleArc" d="M353.8 460.6 A250 250 0 0 1 846.2 460.6"/>
      <path id="contactArc" d="M332.1 551.2 A272 272 0 0 0 867.9 551.2"/>
    </defs>

    <!-- card body -->
    <circle class="card-edge" cx="600" cy="504" r="323" fill="var(--card-black)"/>
    <circle class="card-band" cx="600" cy="504" r="290" fill="url(#ringGradient)"/>
    <circle class="card-inner-ring" cx="600" cy="504" r="236" fill="var(--card-black)"/>
    <circle class="card-window" cx="600" cy="504" r="192" fill="var(--clear-window)" fill-opacity="0.85"/>

    <!-- band lettering -->
    <text class="ring-label ring-label--title">
      <textPath href="#titleArc" startOffset="50%" text-anchor="middle">Light for the Weary Souls</textPath>
    </text>
    <text class="ring-label ring-label--contact">
      <textPath href="#contactArc" startOffset="2%">• 555-382-7194 &#160;&#160;• email@lightfortheweary-mail.org</textPath>
    </text>

    <!-- name in the clear centre -->
    <text class="center-name" x="600" y="496" text-anchor="middle">Light for the</text>
    <text class="center-name" x="600" y="552" text-anchor="middle">Weary Souls</text>
  </svg>
</main>
</body>
</html>
```